Business card design for my company.
I would like the card's background colour to be black. You can also see our web site to get an idea of our brand. https://www.tmwhomecrafting.com.au/
- Name
- Email

```html
<!DOCTYPE html>
<html lang="en">
<head>
<meta charset="utf-8">
<title>TMW Home Crafting – Business Card</title>
<link rel="stylesheet" href="https://fonts.googleapis.com/css2?family=Roboto:wght@400;500&display=swap">
<style>
  :root{
    --page:#f3f3f3;
    --brand-green:#13964a;
    --accent-green:#1a9a4a;
    --card-black:#000000;
    --ink-light:#ffffff;
    --ink-soft:#f1f1f1;
    --shadow:rgba(0,0,0,.35);
  }
  *{margin:0;padding:0;box-sizing:border-box}
  html,body{width:1200px;height:987px;overflow:hidden}
  body{background:var(--page);font-family:"Roboto",Arial,sans-serif;position:relative}

  .card{position:absolute;left:245px;width:709px;border-radius:40px;box-shadow:0 12px 24px var(--shadow)}
  .card--front{top:68px;height:405px;background:var(--brand-green)}
  .card--back{top:514px;height:404px;background:var(--card-black);border:4.5px solid var(--brand-green)}

  .brand-name{position:absolute;color:var(--ink-light);font-weight:500;line-height:1;white-space:nowrap}
  .card--front .brand-name{left:0;right:0;top:170px;text-align:center;font-size:46px}
  .card--back .brand-name{left:30px;width:290px;top:184px;text-align:center;font-size:30px}

  .front-url{position:absolute;left:0;right:0;top:354px;text-align:center;color:var(--ink-light);font-size:17px;letter-spacing:.3px}

  .divider{position:absolute;left:350px;top:66px;width:1px;height:264px;background:var(--accent-green);opacity:.6}

  .contact{position:absolute;left:388px;top:96px;color:var(--ink-soft)}
  .contact__name{font-size:35px;font-weight:400;line-height:1;color:var(--ink-light)}
  .contact__name strong{font-weight:500;color:var(--accent-green)}
  .contact__role{font-size:16.5px;margin-top:2px;letter-spacing:.3px}
  .contact__place{font-size:16.5px;line-height:23px;margin-top:14px;letter-spacing:.3px}
  .contact__list{list-style:none;margin-top:17px;font-size:17px;letter-spacing:.3px}
  .contact__list li{display:flex;align-items:center;height:22.5px;white-space:nowrap}
  .contact__list svg{width:15px;height:15px;margin-right:10px;flex:none}
  .hl{color:var(--accent-green)}
</style>
</head>
<body>
  <section class="card card--front">
    <p class="brand-name">TMW Home Crafting</p>
    <p class="front-url">www.tmwhomecrafting.com.au</p>
  </section>

  <section class="card card--back">
    <p class="brand-name">TMW Home Crafting</p>
    <div class="divider"></div>
    <div class="contact">
      <h1 class="contact__name"><strong>Liam</strong> Hartley</h1>
      <p class="contact__role">General Manager</p>
      <p class="contact__place">Devonport, Tasmania,<br>Australia</p>
      <ul class="contact__list">
        <li>
          <svg viewBox="0 0 24 24" fill="var(--accent-green)" aria-hidden="true"><path d="M6.6 10.8a15 15 0 0 0 6.6 6.6l2.2-2.2a1 1 0 0 1 1-.25 11.4 11.4 0 0 0 3.6.57 1 1 0 0 1 1 1V20a1 1 0 0 1-1 1A17 17 0 0 1 3 4a1 1 0 0 1 1-1h3.5a1 1 0 0 1 1 1c0 1.25.2 2.450.57 3.570a1 1 0 0 1-.25 1z"/></svg>
          0400 512 738
        </li>
        <li>
          <svg viewBox="0 0 24 24" fill="none" stroke="var(--accent-green)" stroke-width="2" aria-hidden="true"><circle cx="12" cy="12" r="9.5"/><path d="M2.5 12h19M12 2.5c3 3 3 16 0 19M12 2.5c-3 3-3 16 0 19"/></svg>
          <span>www.<span class="hl">tmwhomecrafting</span>.com.au</span>
        </li>
        <li>
          <svg viewBox="0 0 24 24" fill="none" stroke="var(--accent-green)" stroke-width="2" aria-hidden="true"><rect x="2.5" y="5" width="19" height="14" rx="1.5"/><path d="M3 6l9 7 9-7"/></svg>
          <span>info@<span class="hl">tmwhomecrafting</span>.com.au</span>
        </li>
      </ul>
    </div>
  </section>
</body>
</html>
```